Book Cover with this title and sub title
Where Auntie Found Her Quiet Orchard
The little book to be smart with your money and help the environment.
Walter P. Brunk Ph. D.
Ellen R. Brunk
Picture below would be on the entire front cover. Words somehow incorporated for easy reading.

```html
<!DOCTYPE html>
<html lang="en">
<head>
<meta charset="utf-8">
<title>Where Auntie Found Her Quiet Orchard — Book Cover</title>
<link rel="stylesheet" href="https://fonts.googleapis.com/css2?family=Bebas+Neue&family=Cinzel:wght@400;500&display=swap">
<style>
  :root {
    --ink-white: #ffffff;
    --honey-gold: #f3b805;
    --petal-yellow: #f5c80f;
    --petal-deep: #e2a006;
    --soil-dark: #2a2016;
    --leaf-dark: #2f3a22;
    --shadow: rgba(0, 0, 0, 0.55);
  }
  html, body {
    margin: 0;
    padding: 0;
    width: 934px;
    height: 1200px;
    overflow: hidden;
    background: var(--soil-dark);
  }
  .cover {
    position: relative;
    width: 934px;
    height: 1200px;
    overflow: hidden;
  }
  .cover-photo {
    position: absolute;
    inset: 0;
    background:
      radial-gradient(ellipse 62% 50% at 52% 66%, var(--petal-yellow) 0%, var(--petal-deep) 55%, rgba(226,160,6,0) 78%),
      radial-gradient(ellipse 40% 30% at 10% 55%, var(--leaf-dark) 0%, rgba(47,58,34,0) 100%),
      linear-gradient(180deg, #3b2e22 0%, var(--soil-dark) 40%, #3a2a14 100%);
  }
  .cover-photo::after {
    content: "";
    position: absolute;
    inset: 0;
    background: linear-gradient(180deg, rgba(0,0,0,0.35) 0%, rgba(0,0,0,0) 45%, rgba(0,0,0,0) 80%, rgba(0,0,0,0.3) 100%);
  }
  .title-block {
    position: absolute;
    top: 0;
    left: 0;
    width: 100%;
    height: 340px;
    margin: 0;
    font-size: 16px;
    font-weight: 400;
    text-align: center;
  }
  .title-block > span {
    position: absolute;
    left: 0;
    width: 100%;
    display: block;
    text-align: center;
    white-space: nowrap;
  }
  .title-lead {
    top: 86px;
    font-family: "Bebas Neue", "Oswald", sans-serif;
    font-size: 92px;
    line-height: 1;
    color: var(--ink-white);
    text-shadow: 0 3px 8px var(--shadow);
  }
  .title-link {
    top: 184px;
    font-family: "Cinzel", serif;
    font-size: 36px;
    letter-spacing: 0.3em;
    line-height: 1;
    color: var(--ink-white);
    text-shadow: 0 2px 6px var(--shadow);
  }
  .title-key {
    top: 224px;
    font-family: "Cinzel", serif;
    font-size: 116px;
    letter-spacing: 0.08em;
    line-height: 1;
    color: var(--honey-gold);
    text-shadow: 0 3px 10px var(--shadow);
  }
  .subtitle {
    position: absolute;
    top: 358px;
    left: 113px;
    width: 698px;
    display: flex;
    align-items: center;
    gap: 20px;
  }
  .subtitle-rule {
    flex: 0 0 92px;
    height: 3px;
    background: var(--ink-white);
  }
  .subtitle-text {
    flex: 1;
    margin: 0;
    font-family: "Bebas Neue", "Oswald", sans-serif;
    font-size: 36px;
    line-height: 1.02;
    text-align: center;
    color: var(--ink-white);
    text-shadow: 0 2px 6px var(--shadow);
  }
  .authors {
    position: absolute;
    top: 1024px;
    left: 0;
    width: 100%;
    margin: 0;
    text-align: center;
    font-family: "Cinzel", serif;
    font-size: 54px;
    line-height: 68px;
    color: var(--ink-white);
    text-shadow: 0 2px 8px var(--shadow);
  }
  .author { display: block; white-space: nowrap; }
</style>
</head>
<body>
  <main class="cover">
    <div class="cover-photo" role="img" aria-label="Close-up photograph of a honeybee gathering nectar on a bright yellow dandelion, dark garden soil and leaves around it"></div>

    <h1 class="title-block">
      <span class="title-lead">WHERE AUNTIE FOUND</span>
      <span class="title-link">HER QUIET</span>
      <span class="title-key">ORCHARD</span>
    </h1>

    <div class="subtitle">
      <span class="subtitle-rule"></span>
      <p class="subtitle-text">The little book to be smart with your<br>money and help the environment.</p>
      <span class="subtitle-rule"></span>
    </div>

    <p class="authors">
      <span class="author">Walter P. Brunk Ph. D.</span>
      <span class="author">Ellen R. Brunk</span>
    </p>
  </main>
</body>
</html>
```